K7 Electrical Services Ltd Web design

I require a web site for my new electrical contracting company. We are customer service orientated. Offering high value electrical installations, design and maintenance. Focused on custom residential and commercial upgrading. Lighting design and application are paramount in our company's services. Industry leading product use and integration are always on the forefront with our customer client services. As well as energy efficiency.

Target Market(s)

Homebuilders, General Contractors, Property management companies, clients, individuals,

Industry/Entity Type

Electric Company

Coding

Coded - Design and coding required

Number of Pages Required

3 page

Requirements
Must have
• Classic, modern, edgy but not trendy . Appeals to the masse.
• 3 page
• home page
• about page
• gallery page
• ability to contact from the webiste
Nice to have
• open to all types of designs that are relative to the construction industry.
• Black, Grey, metallic ice blue and deep purple colours from the logo.
Should not have
• anything cheesy with cartoon light bulb images.

```html
<!DOCTYPE html>
<html lang="en">
<head>
<meta charset="utf-8">
<title>K7 Electrical Services Ltd</title>
<link rel="stylesheet" href="https://fonts.googleapis.com/css2?family=Roboto:wght@300;400;500;700&display=swap">
<style>
  :root {
    --purple: #6b2fa8;
    --purple-light: #9b5ad6;
    --navy: #2b2f5a;
    --muted: #7d7fa3;
    --text: #3a3a4a;
    --white: #ffffff;
    --hero-dark: #2a1d4a;
    --hero-mid: #5a4a86;
    --hero-light: #8f84b4;
  }
  * { box-sizing: border-box; margin: 0; padding: 0; }
  html, body { width: 1200px; height: 676px; overflow: hidden; background: var(--white); }
  body { font-family: "Roboto", Arial, sans-serif; color: var(--text); }

  .site-header {
    height: 68px;
    border-top: 3px solid var(--purple);
    display: flex;
    align-items: center;
    padding: 0 40px;
    background: var(--white);
  }
  .brand { display: flex; align-items: center; gap: 10px; width: 360px; }
  .brand-mark { width: 18px; height: 18px; background: var(--purple); }
  .brand-name { font-size: 20px; font-weight: 500; color: var(--purple); white-space: nowrap; }

  .main-nav { display: flex; gap: 34px; margin-left: 10px; }
  .main-nav a { font-size: 12.5px; color: var(--navy); text-decoration: none; letter-spacing: .2px; }

  .header-actions { margin-left: auto; display: flex; align-items: center; gap: 16px; }
  .chat-link { display: flex; align-items: center; gap: 5px; font-size: 12.5px; color: var(--navy); text-decoration: none; }
  .quote-button {
    background: linear-gradient(90deg, var(--purple), var(--purple-light));
    color: var(--white);
    font-size: 12.5px;
    font-weight: 500;
    padding: 8px 14px;
    border-radius: 16px;
    text-decoration: none;
  }

  .hero {
    position: relative;
    height: 410px;
    display: flex;
    flex-direction: column;
    align-items: center;
    justify-content: center;
    text-align: center;
    color: var(--white);
  }
  .hero-backdrop {
    position: absolute; inset: 0;
    background:
      linear-gradient(100deg, var(--hero-dark) 0%, var(--hero-mid) 45%, var(--hero-light) 70%, var(--hero-dark) 100%);
  }
  .hero-content { position: relative; margin-left: -40px; }
  .hero-eyebrow { font-size: 21px; font-weight: 500; margin-bottom: 18px; }
  .hero-title { font-size: 40px; font-weight: 700; line-height: 1.08; margin-bottom: 26px; }
  .call-button {
    display: inline-block;
    background: var(--white);
    color: var(--purple);
    font-size: 13px;
    font-weight: 500;
    padding: 10px 22px;
    border-radius: 18px;
    text-decoration: none;
  }

  .about {
    display: flex;
    justify-content: space-between;
    padding: 34px 80px 0 90px;
    height: 198px;
  }
  .about-label { font-size: 15px; color: var(--muted); margin-bottom: 10px; }
  .about-title { font-size: 27px; font-weight: 400; color: var(--navy); margin-bottom: 22px; }
  .about-text { font-size: 12px; color: var(--muted); }
  .about-photo {
    width: 330px; height: 190px; margin-top: 14px;
    background: linear-gradient(90deg, #e6e6e8 0%, #f4f4f5 60%, #d9c6a8 100%);
  }
</style>
</head>
<body>
  <header class="site-header">
    <div class="brand">
      <span class="brand-mark"></span>
      <span class="brand-name">K7 Electrical Services Ltd</span>
    </div>
    <nav class="main-nav">
      <a href="#about">ABOUT US</a>
      <a href="#services">SERVICES</a>
      <a href="#gallery">GALLERY</a>
      <a href="#contact">CONTACT</a>
    </nav>
    <div class="header-actions">
      <a class="chat-link" href="#chat">Chat
        <svg width="13" height="12" viewBox="0 0 13 12" aria-hidden="true">
          <path d="M1.5 1.5h10v6.5H5l-3 2.5V8H1.5z" fill="none" stroke="#2b2f5a" stroke-width="1.2" stroke-linejoin="round"/>
        </svg>
      </a>
      <a class="quote-button" href="#quote">Request a Quote</a>
    </div>
  </header>

  <section class="hero">
    <div class="hero-backdrop" role="img" aria-label="Photo of a modern residential building at dusk with garden lighting, tinted purple"></div>
    <div class="hero-content">
      <p class="hero-eyebrow">Your Residential Electrical Experts</p>
      <h1 class="hero-title">Keeping Your Family Safe &amp;<br>Comfortable</h1>
      <a class="call-button" href="tel:+18005550142">Call: +1 (800) 555 01 42</a>
    </div>
  </section>

  <section class="about" id="about">
    <div class="about-copy">
      <p class="about-label">About Us</p>
      <h2 class="about-title">Who we are ?</h2>
      <p class="about-text">We have many years of foreign experience on projects for affluent clients.</p>
    </div>
    <div class="about-photo" role="img" aria-label="Portrait photo of the company founder in a bright interior"></div>
  </section>
</body>
</html>
```